Business card for Crestline Bathrooms

Please design a business card for our bathroom renovation business. You can use my existing logo, but if you have an idea to modernize it, I would like to see it. Please see attached files first. I would like to use the blue and the orange theme. I like the concept of using the shower head in the logo. Please find following a design (or two) that I have been trying to create with my limited resources. That design was for a sign, but I was going to adopt it and use it as a business card as well. I like the concept of the water splash but I don’t think it “flows” nicely together with the logo. Another thought is that maybe creating the logo out of water splash could work and have a dramatic effect (like the water text and the butterfly picture attached with similar background instead of white). If the above doesn’t work I would like to see a modern simplified design. One of the attached files named as the unwanted business card has all the details that I want included in the business card. Please note that it is two sided.
Updates

I am very thankful for the designs that I have received, but they are very similar and only a couple of attempts to do something with the water splash as per my original brief. Modernizing the logo and having it made out of out of water splash with the orange as color accent could work and have a dramatic effect (like the water text and the butterfly picture attached with similar background instead of white). Please do not use the butterfly itself! This is just an example that images can be created out of water splash.

Contact Information for Business Card

all the details are on the unwonted business card file included

Colors
3176b5

Requirements
Nice to have
• Copied from the brief:
• ... maybe creating the logo out of water splash could work and have a dramatic effect (like the water text and the butterfly picture attached with similar background instead of white). Please do not use the butterfly itself!
Should not have
• I am getting designs with a butterfly. The butterfly picture was an example of creating something from a water splash. The butterfly itself has no association with anything other than the concept of creating a logo out of water splash. Sorry, I thought I was clear in the brief.

```html
<!DOCTYPE html>
<html lang="en">
<head>
<meta charset="UTF-8">
<title>Crestline Bathrooms – Business Card</title>
<link rel="stylesheet" href="https://fonts.googleapis.com/css2?family=Roboto:wght@400;500;700&family=Roboto+Condensed:wght@400&display=swap">
<style>
  :root {
    --stage: #3b3b3d;
    --card: #ffffff;
    --navy: #1c3f6a;
    --blue: #1f5580;
    --blue-deep: #173f63;
    --blue-light: #3176b5;
    --coral: #e9786b;
    --ink: #4a4a4a;
    --rule: #2b5c8c;
  }
  * { box-sizing: border-box; margin: 0; padding: 0; }
  html, body {
    width: 1200px; height: 900px; overflow: hidden;
    background: var(--stage);
    font-family: "Roboto", Arial, sans-serif;
  }
  .stage {
    position: relative; width: 1200px; height: 900px;
  }
  .card {
    position: absolute; left: 250px;
    width: 700px; height: 400px;
    background: var(--card);
    border-radius: 22px;
    overflow: hidden;
    box-shadow: 0 10px 30px rgba(0,0,0,.35);
  }
  .card--back { top: 35px; }
  .card--front { top: 465px; }

  .brand-name {
    font-family: "Roboto", Arial, sans-serif;
    font-weight: 700;
    color: var(--navy);
    line-height: 1.05;
    display: flex; align-items: center; gap: 12px;
  }
  .brand-name .brand-dot {
    width: 16px; height: 16px; border-radius: 50%;
    background: var(--coral); flex: none;
  }

  /* Back side */
  .card--back .brand-name {
    position: absolute; left: 70px; top: 62px; font-size: 34px;
  }
  .card--back .divider {
    position: absolute; left: 390px; top: 48px;
    width: 2px; height: 120px; background: var(--rule);
  }
  .partner-badges {
    position: absolute; left: 430px; top: 60px;
    display: flex; flex-direction: column; align-items: center; gap: 18px;
  }
  .partner-badge--block {
    width: 190px; height: 40px; background: var(--navy); border-radius: 3px;
  }
  .partner-badge--seal {
    width: 46px; height: 46px; background: var(--navy); border-radius: 50%;
  }
  .services {
    position: absolute; left: 70px; top: 200px;
    list-style: none;
    font-family: "Roboto Condensed", Arial, sans-serif;
    font-size: 19px; color: var(--ink);
    text-transform: uppercase; line-height: 1.45; letter-spacing: .3px;
  }
  .services li::before { content: "> "; }

  /* Front side */
  .card--front .brand-name {
    position: absolute; left: 60px; top: 60px; font-size: 36px;
  }
  .wave { position: absolute; inset: 0; }
  .contact {
    position: absolute; right: 50px; top: 215px;
    text-align: right; color: #ffffff;
  }
  .contact .person {
    font-size: 27px; font-weight: 700; letter-spacing: .8px;
    text-transform: uppercase; margin-bottom: 8px;
  }
  .contact .address { font-size: 18px; line-height: 1.3; margin-bottom: 8px; }
  .contact .line {
    font-size: 18px; line-height: 1.45;
    display: flex; justify-content: flex-end; align-items: center; gap: 10px;
  }
  .contact .line svg { width: 15px; height: 15px; flex: none; }
</style>
</head>
<body>
<main class="stage">

  <section class="card card--back" aria-label="Card back">
    <div class="brand-name"><span class="brand-dot"></span>Crestline<br>Bathrooms</div>
    <div class="divider"></div>
    <div class="partner-badges" aria-label="Industry memberships">
      <div class="partner-badge--block"></div>
      <div class="partner-badge--seal"></div>
    </div>
    <ul class="services">
      <li>Complete bathroom renovations &amp; remodelling</li>
      <li>Highly skilled &amp; qualified tradespeople</li>
      <li>Professional service from concept to completion</li>
      <li>All work guaranteed</li>
    </ul>
  </section>

  <section class="card card--front" aria-label="Card front">
    <div class="brand-name"><span class="brand-dot"></span>Crestline<br>Bathrooms</div>

    <svg class="wave" viewBox="0 0 700 400" preserveAspectRatio="none" aria-hidden="true">
      <defs>
        <linearGradient id="splash-tone" x1="0" y1="0" x2="1" y2="1">
          <stop offset="0" stop-color="#2f6a97"/>
          <stop offset=".5" stop-color="#1f5580"/>
          <stop offset="1" stop-color="#173f63"/>
        </linearGradient>
      </defs>
      <path d="M0,255 Q320,150 700,200 L700,400 L0,400 Z" fill="var(--coral)"/>
    </svg>
    <svg class="wave" viewBox="0 0 700 400" preserveAspectRatio="none" role="img" aria-label="Water splash photograph in deep blue tones">
      <path d="M0,275 Q320,168 700,218 L700,400 L0,400 Z" fill="url(#splash-tone)"/>
    </svg>

    <div class="contact">
      <p class="person">Daniel Marovic</p>
      <p class="address">PO Box 418<br>Larkfield 2871</p>
      <p class="line">0400 555 218 | 6200 0147
        <svg viewBox="0 0 16 16" aria-hidden="true"><path d="M4 1.5 6 5 4.6 6.4a8 8 0 0 0 5 5L11 10l3.5 2-.8 2.3C8 14.5 1.5 8 1.7 2.3Z" fill="#fff"/></svg>
      </p>
      <p class="line">daniel@crestlinebathrooms.com.au
        <svg viewBox="0 0 16 16" aria-hidden="true"><rect x="1.5" y="3.5" width="13" height="9" fill="none" stroke="#fff" stroke-width="1.4"/><path d="M1.5 3.5 8 9l6.5-5.5" fill="none" stroke="#fff" stroke-width="1.4"/></svg>
      </p>
      <p class="line">www.crestlinebathrooms.com.au
        <svg viewBox="0 0 16 16" aria-hidden="true"><circle cx="8" cy="8" r="6.3" fill="none" stroke="#fff" stroke-width="1.3"/><ellipse cx="8" cy="8" rx="2.8" ry="6.3" fill="none" stroke="#fff" stroke-width="1.1"/><path d="M1.7 8h12.6" stroke="#fff" stroke-width="1.1"/></svg>
      </p>
    </div>
  </section>

</main>
</body>
</html>
```